Kesso Tea Premium Matcha brand Label

This is a label design project for a luxury tea brand. Feel free to be creative within the guidelines.
Attached to this project is a document called “Private Label Design Requirements” with the design guidelines and template. There is another document called "Kesso Tea Packaging Instructions" this has more details necessary to stick to the guidelines in the first document.

I have also attached the certifications to be included as well as different variations of the logo for you to use.

If you have any questions, I am here.
Updates

Need extra days to review

Target Market(s)

Young, active, fun, enjoy the finer things

```html
<!DOCTYPE html>
<html lang="en">
<head>
<meta charset="utf-8">
<title>Kesso Tea Premium Organic Ceremonial Matcha Label</title>
<link href="https://fonts.googleapis.com/css2?family=Raleway:wght@600;700;800&display=swap" rel="stylesheet">
<style>
  :root {
    --stage: #bcc8b7;
    --label-base: #f8f7f5;
    --leaf-light: #e3eedb;
    --leaf-mid: #cfe3c1;
    --forest: #4b5e23;
    --accent: #b9d24c;
    --white: #ffffff;
  }
  html, body {
    margin: 0;
    padding: 0;
    width: 1200px;
    height: 803px;
    overflow: hidden;
    background: var(--stage);
    font-family: "Raleway", Arial, sans-serif;
  }
  .label {
    position: absolute;
    left: 30px;
    top: 290px;
    width: 1140px;
    height: 222px;
    background: var(--label-base);
    overflow: hidden;
    box-shadow: 0 6px 10px rgba(0,0,0,0.18);
  }
  .leaf-pattern {
    position: absolute;
    inset: 0;
    background: linear-gradient(90deg, var(--leaf-mid) 0%, var(--leaf-light) 35%, var(--label-base) 50%, var(--leaf-light) 65%, var(--leaf-mid) 100%);
  }
  .distributor-band {
    position: absolute;
    left: 0;
    top: 113px;
    width: 292px;
    height: 64px;
    background: var(--forest);
    border-radius: 0 32px 32px 0;
    color: var(--white);
    font-weight: 700;
    font-size: 10px;
    line-height: 16.5px;
    box-sizing: border-box;
    padding: 8px 0 0 79px;
  }
  .brand-seal {
    position: absolute;
    left: 484px;
    top: 25px;
    width: 172px;
    height: 172px;
    border-radius: 50%;
    background: var(--white);
  }
  .seal-ring {
    position: absolute;
    left: 18px;
    top: 18px;
    width: 132px;
    height: 132px;
    border: 2px solid var(--forest);
    border-radius: 50%;
  }
  .brand-dot {
    position: absolute;
    left: 72px;
    top: 34px;
    width: 28px;
    height: 28px;
    border-radius: 50%;
    background: var(--forest);
  }
  .brand-name {
    position: absolute;
    left: 0;
    width: 100%;
    top: 66px;
    text-align: center;
    font-weight: 800;
    font-size: 14px;
    color: #1f1f1f;
  }
  .product-banner {
    position: absolute;
    left: 3px;
    top: 102px;
    width: 166px;
    height: 35px;
    background: var(--forest);
    color: var(--white);
    font-weight: 700;
    font-size: 11px;
    line-height: 14px;
    text-align: center;
    box-sizing: border-box;
    padding-top: 4px;
    letter-spacing: 0.2px;
  }
  .net-weight {
    position: absolute;
    left: 0;
    width: 100%;
    top: 138px;
    text-align: center;
    font-weight: 700;
    font-size: 7px;
    color: #1f1f1f;
  }
  .info-panel {
    position: absolute;
    left: 805px;
    top: 0;
    width: 252px;
    height: 201px;
    background: var(--forest);
    border-radius: 0 0 45px 45px;
    color: var(--white);
  }
  .panel-heading {
    position: absolute;
    left: 6px;
    margin: 0;
    font-weight: 700;
    font-size: 12.5px;
    color: var(--accent);
  }
  .ingredients-heading { top: 38px; }
  .instructions-heading { top: 79px; }
  .ingredients-text {
    position: absolute;
    left: 15px;
    top: 58px;
    margin: 0;
    font-weight: 700;
    font-size: 9.6px;
  }
  .instruction-list {
    position: absolute;
    left: 15px;
    top: 97px;
    margin: 0;
    padding: 0;
    list-style: none;
    font-weight: 700;
    font-size: 9.6px;
    line-height: 12.3px;
  }
  .instruction-list li::before { content: "\2022\00a0"; }
  .cert-badge {
    position: absolute;
    background: var(--white);
  }
  .cert-round { left: 147px; top: 146px; width: 32px; height: 32px; border-radius: 50%; }
  .cert-square { left: 185px; top: 148px; width: 37px; height: 28px; }
</style>
</head>
<body>
  <main class="label">
    <div class="leaf-pattern" role="img" aria-label="Repeating pattern of green tea leaves on a white background"></div>

    <section class="distributor-band">
      <div>Distributed by Kesso Tea Co. | Atlanta, Ga</div>
      <div>Certified Organic by Verdana Certifiers</div>
      <div>PRODUCT OF JAPAN</div>
    </section>

    <section class="brand-seal">
      <div class="seal-ring"></div>
      <div class="brand-dot"></div>
      <div class="brand-name">Kesso Tea</div>
      <div class="product-banner">PREMIUM ORGANIC<br>CEREMONIAL MATCHA</div>
      <div class="net-weight">Net Wt: 30g</div>
    </section>

    <section class="info-panel">
      <h2 class="panel-heading ingredients-heading">Ingredients</h2>
      <p class="ingredients-text">Premium Organic Japanese Matcha Green Tea</p>
      <h2 class="panel-heading instructions-heading">Instructions</h2>
      <ul class="instruction-list">
        <li>2 tsp of Matcha</li>
        <li>2oz of Water (170-180 degrees F)</li>
        <li>Whisk in a W formation until frothy</li>
        <li>Sweeten to taste</li>
      </ul>
      <div class="cert-badge cert-round" role="img" aria-label="Organic certification badge"></div>
      <div class="cert-badge cert-square" role="img" aria-label="Non-GMO verification badge"></div>
    </section>
  </main>
</body>
</html>
```